Business card design for a teacher - double sided, sleek design.

My name is Lina and I am an online Arabic language teacher. I am looking for a beautiful business card design for my online teaching business.

The cards will be printed in 85mm x 55mm size.
The card can be either portrait or landscape.

The design should contain my logo on one side and information on the other.

The design needs to be clean and modern. Use of subtle Arabic geometric patterns would be nice. Icons for the social media information on the card should also match the design theme.

My logo font is Consolas, which is a Monospace font.

Business card design should be delivered with editable PSD or EPS files in the handover.

Thanks

Lina

----

Information on the back:

URL: www.speakwithnadia.net [this should stand out more than other details]
Email: info@speakwithnadia.net
Instagram: @speakwithnadia
Facebook: facebook.com/speakwithnadia
Skype: speakwithnadia

My brand colours are shown in the logo attached. These are:
- Teal green - 4DC9C1
- Mango yellow - FFD600

Target Market(s)

- Young professionals
- Expatriates
- Women and Men

Industry/Entity Type

Education

Contact Information for Business Card

Information on the back:

Skype: speakwithnadia

- Teal green - 4DC9C1
- Mango yellow - FFD600

Font styles to use
Other font styles liked:
• Any font complimentary to my logo font which is a Monospace font called Consolas.

Colors

Designer to choose colors to be used in the design.

Requirements
Must have
• - Aesthetically pleasing look
• - Complimentary design with existing logo
Nice to have
• Arabic geometrical patterns

```html
<!DOCTYPE html>
<html lang="en">
<head>
<meta charset="utf-8">
<title>Speak with Nadia – Business Card</title>
<link rel="stylesheet" href="https://fonts.googleapis.com/css2?family=Montserrat:wght@400;700&display=swap">
<style>
  :root {
    --backdrop: #1b1b1d;
    --card: #1f1f21;
    --card-light: #2a2a2d;
    --teal: #4dc9c1;
    --mango: #ffd600;
    --ink: #f2f2f2;
  }
  * { margin: 0; padding: 0; box-sizing: border-box; }
  html, body { width: 1200px; height: 900px; overflow: hidden; }
  body {
    background: var(--backdrop);
    font-family: "Montserrat", sans-serif;
    color: var(--ink);
    position: relative;
  }
  .card {
    position: absolute;
    left: 300px;
    width: 600px;
    height: 388px;
    background: var(--card);
    border-bottom: 6px solid var(--mango);
    overflow: hidden;
  }
  .card--front { top: 42px; }
  .card--back { top: 470px; background: linear-gradient(135deg, #1c1c1e 0%, #262628 60%, #1c1c1e 100%); }

  .geo-pattern {
    position: absolute;
    inset: 0;
    background: linear-gradient(135deg, #1d1d1f 0%, var(--card-light) 55%, #1d1d1f 100%);
  }

  .brand {
    position: absolute;
    display: flex;
    align-items: center;
    gap: 14px;
  }
  .brand__dot {
    border-radius: 50%;
    background: var(--teal);
    flex: none;
  }
  .brand__name {
    font-family: "Montserrat", sans-serif;
    font-weight: 700;
    color: var(--ink);
    line-height: 1.1;
    white-space: nowrap;
  }
  .card--front .brand { left: 0; right: 0; top: 166px; justify-content: center; }
  .card--front .brand__dot { width: 40px; height: 40px; }
  .card--front .brand__name { font-size: 40px; }

  .card--back .brand { left: 40px; top: 170px; }
  .card--back .brand__dot { width: 22px; height: 22px; }
  .card--back .brand__name { font-size: 20px; }

  .divider {
    position: absolute;
    left: 260px;
    top: 110px;
    width: 2px;
    height: 170px;
    background: var(--mango);
  }
  .contact {
    position: absolute;
    left: 295px;
    top: 112px;
  }
  .contact__name {
    font-weight: 700;
    font-size: 36px;
    color: var(--mango);
    letter-spacing: 0.04em;
    text-transform: uppercase;
    margin-bottom: 14px;
  }
  .contact__list { list-style: none; }
  .contact__item {
    display: flex;
    align-items: center;
    gap: 12px;
    font-size: 17px;
    line-height: 24px;
  }
  .contact__icon { width: 14px; height: 14px; flex: none; }
  .contact__dot { width: 9px; height: 9px; margin: 0 2.5px; background: var(--mango); border-radius: 50%; flex: none; }
</style>
</head>
<body>
  <section class="card card--front">
    <div class="geo-pattern" role="img" aria-label="Subtle dark Arabic geometric pattern"></div>
    <div class="brand">
      <span class="brand__dot"></span>
      <span class="brand__name">Speak with Nadia</span>
    </div>
  </section>

  <section class="card card--back">
    <div class="brand">
      <span class="brand__dot"></span>
      <span class="brand__name">Speak with Nadia</span>
    </div>
    <span class="divider"></span>
    <div class="contact">
      <h1 class="contact__name">Lina</h1>
      <ul class="contact__list">
        <li class="contact__item"><span class="contact__dot"></span>@speakwithnadia</li>
        <li class="contact__item"><span class="contact__dot"></span>facebook.com/speakwithnadia</li>
        <li class="contact__item"><span class="contact__dot"></span>speakwithnadia</li>
        <li class="contact__item">
          <svg class="contact__icon" viewBox="0 0 14 14" fill="none" stroke="#ffd600" stroke-width="1.4"><rect x="1" y="3" width="12" height="8"/><path d="M1 3l6 5 6-5"/></svg>
          info@speakwithnadia.net
        </li>
        <li class="contact__item">
          <svg class="contact__icon" viewBox="0 0 14 14" fill="none" stroke="#ffd600" stroke-width="1.2"><circle cx="7" cy="7" r="6"/><ellipse cx="7" cy="7" rx="2.6" ry="6"/><path d="M1 7h12"/></svg>
          www.speakwithnadia.net
        </li>
      </ul>
    </div>
  </section>
</body>
</html>
```